BUSINESS CARD FOR GUITAR SCHOOL

I would like to design a business card for my Guitar Music School. The school is called "Pluck & Lantern".

The card should be yellow.

Target Market(s)

18-35 years old

Industry/Entity Type

School

Contact Information for Business Card

I would like to design a business card for my Guitar Music School. The school is called "Pluck & Lantern". The card should be yellow.

Card must be consistent with my website design: www.pluckandlantern.com.sg

Requirements
Must have
• 1) Name of Company
• 2) Company Logo
• 3) Name of Employee
• 4) Position of Employee
• 5) Contact Number
• 6) Address
Nice to have
• Creative Design
• Card must be consistent with my website design: www.pluckandlantern.com.sg
Should not have
• Boring Design

```html
<!DOCTYPE html>
<html lang="en">
<head>
<meta charset="utf-8">
<title>Pluck &amp; Lantern – Business Card</title>
<link rel="stylesheet" href="https://fonts.googleapis.com/css2?family=Ubuntu:wght@700&family=Oswald:wght@300;400&display=swap">
<style>
  :root {
    --yellow: #f3d01c;
    --ink: #222222;
    --paper: #ffffff;
    --stage: #eeeeee;
    --muted: #8a8a8a;
    --slogan-tone: #d6d6d6;
  }
  * { margin: 0; padding: 0; box-sizing: border-box; }
  html, body { width: 1200px; height: 1000px; overflow: hidden; background: var(--stage); }
  .canvas { position: relative; width: 1200px; height: 1000px; }

  .card { position: absolute; width: 760px; height: 420px; background: var(--paper); overflow: hidden; }

  /* Front */
  .card-front { left: 90px; top: 82px; }
  .front-yellow { position: absolute; left: 0; top: 0; width: 495px; height: 100%; background: var(--yellow); }
  .brand-name {
    position: absolute; left: 0; top: 0; width: 495px; height: 100%;
    display: flex; align-items: center; justify-content: center;
    color: var(--ink); font-family: "Ubuntu", sans-serif; font-weight: 700;
    font-size: 52px; letter-spacing: -1px; white-space: nowrap;
  }
  .slogan-art { position: absolute; left: 530px; top: 145px; width: 185px; height: 140px; background: var(--slogan-tone); border-radius: 4px; }

  /* Back */
  .card-back { left: 340px; top: 500px; width: 770px; }
  .card-back svg { display: block; }
  .contact { position: absolute; left: 220px; top: 45px; width: 330px; text-align: center; color: var(--paper); font-family: "Oswald", sans-serif; font-weight: 300; }
  .contact-name { font-size: 29px; font-weight: 400; margin-top: 20px; }
  .contact-role { font-size: 17px; color: var(--muted); margin-bottom: 40px; }
  .contact-line { font-size: 22px; line-height: 1.3; }
</style>
</head>
<body>
<div class="canvas">

  <section class="card card-front">
    <div class="front-yellow"></div>
    <div class="brand-name">Pluck &amp; Lantern</div>
    <div class="slogan-art" role="img" aria-label="Hand-lettered three-line slogan in black brush strokes"></div>
  </section>

  <section class="card card-back">
    <svg width="770" height="420" viewBox="0 0 770 420" aria-hidden="true">
      <rect class="back-yellow" x="0" y="0" width="385" height="420" fill="var(--yellow)"/>
      <g class="strings" stroke="var(--ink)" stroke-width="1">
        <line x1="0" y1="150" x2="770" y2="150"/>
        <line x1="0" y1="188" x2="770" y2="188"/>
        <line x1="0" y1="226" x2="770" y2="226"/>
        <line x1="0" y1="264" x2="770" y2="264"/>
        <line x1="0" y1="302" x2="770" y2="302"/>
      </g>
      <circle class="ring-outer" cx="385" cy="210" r="182" fill="var(--yellow)"/>
      <circle class="ring-inner" cx="385" cy="210" r="173" fill="var(--paper)"/>
      <circle class="disc" cx="385" cy="210" r="165" fill="var(--ink)"/>
    </svg>
    <div class="contact">
      <div class="contact-name">Daniel Okafor</div>
      <div class="contact-role">Director</div>
      <div class="contact-line">27 Kembangan Lane</div>
      <div class="contact-line">Harbour Block B #05-12</div>
      <div class="contact-line">Singapore 418273</div>
      <div class="contact-line">Tel: +65 9481 2750</div>
    </div>
  </section>

</div>
</body>
</html>
```